New Dental Office Needs an Attractive and user friendly Website Designed

I need a website for a new dental office. The Name is Harrowfield Dentistry. I would like a Modern design with a user friendly interface and usability.
I would like a landing page, a page that lists the services we offer: Cosmetic Dentistry, Implants, Dental Hygiene, Emergency Services, Restorations, Dentures
Target Market(s)
Mid to upper class
Industry/Entity Type
Dentistry
Coding
Number of Pages Required
1 page
Requirements
Must have
- Landing page that has a scheduling option, Procedures, operating hours, and contact us info
Nice to have
- Appealing design, Soft comforting colors. Easy to navigate page, Modern and professional.

```html
<!DOCTYPE html>
<html lang="en">
<head>
<meta charset="utf-8">
<title>Harrowfield Dentistry</title>
<link href="https://fonts.googleapis.com/css2?family=Poppins:wght@300;400;500;600&display=swap" rel="stylesheet">
<style>
:root{
  --accent:#a8948a;
  --accent-light:#b5a296;
  --band:#8b7e78;
  --ink:#2f2f2f;
  --muted:#6b6b6b;
  --soft:#f3f1ef;
  --white:#ffffff;
  --line:#d9d3ce;
}
*{box-sizing:border-box;margin:0;padding:0}
html,body{width:1200px;height:4231px;overflow:hidden}
body{position:relative;font-family:'Poppins',sans-serif;color:var(--ink);background:var(--white)}
.abs{position:absolute}
.btn{position:absolute;display:flex;align-items:center;justify-content:center;background:var(--accent);color:var(--white);font-size:11px;font-weight:500;letter-spacing:.3px;text-transform:uppercase;border-radius:5px}
.eyebrow{font-size:12px;color:var(--accent);text-transform:uppercase;letter-spacing:.3px}
.center{left:0;width:1200px;text-align:center}

/* header */
.hero-bg{left:0;top:0;width:1200px;height:645px;background:linear-gradient(100deg,#ebe8e5 0%,#f2f0ee 45%,#f7f6f5 100%)}
.logo{text-align:center;font-family:'Poppins',sans-serif;font-weight:500;color:var(--ink)}
.logo .name{font-size:26px;line-height:1}
.logo .sub{font-size:12px;letter-spacing:4px;margin-top:3px}
.site-logo{left:150px;top:20px}
.nav{left:434px;top:32px;display:flex;gap:36px;font-size:13px}
.nav a{color:var(--ink);text-decoration:none}
.nav a.active{color:var(--accent)}
.book-top{left:877px;top:21px;width:162px;height:42px;font-size:11px}

/* hero */
.hero-title{left:160px;top:228px;font-size:42px;font-weight:400;line-height:1.4}
.hero-title span{display:block;color:var(--accent-light);font-weight:600;font-size:48px;line-height:1.1}
.hero-text{left:160px;top:350px;width:450px;font-size:13.5px;line-height:1.35;color:var(--muted)}
.hero-btn{left:161px;top:410px;width:161px;height:37px}
.hero-arch{left:719px;top:210px;width:397px;height:435px;border-radius:200px 200px 0 0;background:var(--accent-light)}
.hero-photo{left:735px;top:115px;width:360px;height:530px;border-radius:170px 170px 0 0;background:linear-gradient(180deg,rgba(255,255,255,0) 0%,rgba(244,242,240,.85) 40%,#eef0f3 100%)}
.hero-tools{left:575px;top:430px;width:180px;height:250px;border-radius:40px;background:linear-gradient(160deg,#e7e8ea,#c9cbcf)}
.info-card{top:604px;height:87px;display:flex;align-items:center;gap:14px;padding:0 22px;color:var(--white)}
.info-hours{left:673px;width:246px;background:#a7948a;border-radius:10px 0 0 10px}
.info-call{left:919px;width:243px;background:#d9cbc1;border-radius:0 10px 10px 0;color:var(--ink)}
.info-card b{display:block;font-size:13px;font-weight:600}
.info-card small{font-size:11px}

/* about */
.about-photo{left:182px;top:767px;width:394px;height:500px;border-radius:190px 190px 0 0;background:linear-gradient(180deg,#e9eaec 0%,#7aa1c6 55%,#294a78 100%)}
.about-eyebrow{left:661px;top:862px}
.about-title{left:661px;top:890px;font-size:29px;font-weight:400;line-height:1.27;width:420px}
.about-text{left:662px;width:370px;font-size:13px;line-height:1.5;color:#444}
.about-btn{left:662px;top:1167px;width:161px;height:40px}

/* services */
.services-band{left:0;top:1359px;width:1200px;height:862px;background:var(--band)}
.section-title{font-size:29px;font-weight:400;line-height:1.2}
.section-sub{font-size:13px;line-height:1.5;color:var(--muted)}
.svc{position:absolute;width:214px;height:260px;background:var(--white);border-radius:107px 107px 0 0;text-align:center}
.svc svg{margin-top:32px}
.svc h3{font-size:15px;font-weight:600;margin-top:12px}
.svc p{font-size:11px;color:#8a8a8a;line-height:1.2;margin:6px auto 0;width:180px}
.svc .btn{left:42px;bottom:27px;width:130px;height:34px;text-transform:none;font-size:11px}

/* testimonials */
.arc{left:0;top:0}
.doc-photo{left:440px;top:2418px;width:320px;height:455px;border-radius:160px 160px 20px 20px;background:linear-gradient(180deg,#f1efed 0%,#c9b7ab 55%,#dcdde0 100%)}
.quote{position:absolute;width:220px;text-align:center}
.quote h4{font-size:15px;font-weight:400;margin-bottom:12px}
.quote p{font-size:12px;color:#555;line-height:1.2}
.quote i{display:block;font-style:normal;color:var(--accent);font-size:40px;line-height:.9;margin-top:8px;font-weight:600;height:26px}

/* team */
.team-bg{left:0;top:2922px;width:1200px;height:575px;background:var(--soft)}
.member{position:absolute;top:3117px;width:200px;height:245px}
.member .photo{position:absolute;inset:0}
.member .tag{position:absolute;left:14px;right:14px;bottom:13px;height:66px;background:var(--white);border-radius:8px;text-align:center;padding-top:14px}
.member .tag b{display:block;font-size:14px;font-weight:500}
.member .tag small{font-size:11px;color:#888}
.team-btn{left:520px;top:3400px;width:161px;height:41px}

/* booking */
.book-band{left:0;top:3497px;width:1200px;height:471px;background:var(--band)}
.map{left:159px;top:3556px;width:414px;height:346px;background:linear-gradient(135deg,#f1f0ee,#e3e4e6)}
.book-title{left:614px;top:3555px;width:417px;text-align:center;font-size:28px;font-weight:400;color:var(--white)}
.field{position:absolute;background:var(--white);font-size:11px;color:#9a9a9a;padding:10px 16px}
.book-btn{left:722px;top:3866px;width:201px;height:34px;background:var(--white);color:#555;border-radius:0;font-size:11px}

/* footer */
.foot-logo{left:0;width:1200px;top:4003px}
.foot-nav{left:0;width:1200px;top:4080px;display:flex;justify-content:center;font-size:12px}
.foot-nav a{color:var(--ink);text-decoration:none;width:96px;text-align:center}
.contact{position:absolute;top:4124px;display:flex;align-items:center;gap:10px;font-size:12px;white-space:nowrap}
.ci{width:28px;height:28px;border-radius:50%;background:#777;display:flex;align-items:center;justify-content:center}
.social{left:0;width:1200px;top:4184px;display:flex;justify-content:center;gap:30px}
.social span{width:14px;height:14px;border:1.5px solid #777;border-radius:50%}
</style>
</head>
<body>

<!-- Header & hero -->
<div class="abs hero-bg" role="img" aria-label="Soft faded photo of a patient in the dental chair"></div>
<div class="abs logo site-logo"><div class="name">Harrowfield</div><div class="sub">DENTISTRY</div></div>
<nav class="abs nav">
  <a class="active" href="#">Home</a><a href="#">About Us</a><a href="#">Services</a><a href="#">Dentists</a><a href="#">Contact Us</a>
</nav>
<a class="btn book-top">Book Appointment</a>

<h1 class="abs hero-title">HIGH QUALITY AND<span>PAINLESS DENTISTRY</span></h1>
<p class="abs hero-text">If you are in need of high-quality, professional and friendly dental care, look no further than our clinic.</p>
<a class="btn hero-btn">Learn More</a>

<div class="abs hero-arch"></div>
<div class="abs hero-photo" role="img" aria-label="Smiling dentist in a white coat with a stethoscope"></div>
<div class="abs hero-tools" role="img" aria-label="Tooth model with dental mirror and probe"></div>

<div class="abs info-card info-hours">
  <svg width="40" height="40" viewBox="0 0 40 40" fill="none" stroke="#fff" stroke-width="2.5"><circle cx="20" cy="20" r="17"/><path d="M20 10v10l7 5"/></svg>
  <div><b>Opening Hours</b><small>Mon to Sat 08:00 - 20:00</small></div>
</div>
<div class="abs info-card info-call">
  <svg width="38" height="38" viewBox="0 0 24 24" fill="#fff"><path d="M6.6 10.8a15.1 15.1 0 0 0 6.6 6.6l2.2-2.2a1 1 0 0 1 1-.25 11.4 11.4 0 0 0 3.6.57 1 1 0 0 1 1 1V20a1 1 0 0 1-1 1A17 17 0 0 1 3 4a1 1 0 0 1 1-1h3.5a1 1 0 0 1 1 1c0 1.25.2 2.45.57 3.57a1 1 0 0 1-.25 1z"/></svg>
  <div><b>Need Dental Services?</b><small>Call: +1 555 014 2290</small></div>
</div>

<!-- About -->
<div class="abs about-photo" role="img" aria-label="Two smiling dentists in scrubs"></div>
<p class="abs eyebrow about-eyebrow">About Us</p>
<h2 class="abs about-title">PROFESSIONALS AND PERSONALIZED DENTAL EXCELLENCE</h2>
<p class="abs about-text" style="top:1010px">Welcome to our Maplecrest Chapters dedicated to empowering pet owners with valuable knowledge and resources.</p>
<p class="abs about-text" style="top:1081px">Welcome to our Maplecrest Chapters dedicated to empowering pet owners with valuable knowledge and resources.</p>
<a class="btn about-btn">Learn More</a>

<!-- Services -->
<section class="abs services-band"></section>
<p class="abs eyebrow center" style="top:1430px;color:#fff">Our Services</p>
<h2 class="abs section-title center" style="top:1456px;color:#fff">COMPLETE CARE FOR EVERY SMILE</h2>
<p class="abs section-sub center" style="top:1504px;color:#eee">Welcome to our Maplecrest Chapters dedicated to empowering pet owners with<br>valuable knowledge and resources.</p>

<div class="svc" style="left:228px;top:1584px"><svg width="64" height="70" viewBox="0 0 64 70" fill="none" stroke="#9a877c" stroke-width="2"><path d="M14 8c-6 2-8 12-4 20 3 6 3 14 5 22 1 4 5 4 6 0l3-12c1-3 5-3 6 0l3 12c1 4 5 4 6 0 2-8 2-16 5-22 4-8 2-18-4-20-6-2-10 2-13 2s-7-4-13-2z"/></svg><h3>Implants</h3><p>It is a long established fact that a will be distracted.</p><a class="btn">View Details</a></div>
<div class="svc" style="left:494px;top:1584px"><svg width="64" height="70" viewBox="0 0 64 70" fill="none" stroke="#9a877c" stroke-width="2"><path d="M14 8c-6 2-8 12-4 20 3 6 3 14 5 22 1 4 5 4 6 0l3-12c1-3 5-3 6 0l3 12c1 4 5 4 6 0 2-8 2-16 5-22 4-8 2-18-4-20-6-2-10 2-13 2s-7-4-13-2z"/></svg><h3>Cosmetic Dentistry</h3><p>It is a long established fact that a will be distracted.</p><a class="btn">View Details</a></div>
<div class="svc" style="left:758px;top:1584px"><svg width="64" height="70" viewBox="0 0 64 70" fill="none" stroke="#9a877c" stroke-width="2"><path d="M14 8c-6 2-8 12-4 20 3 6 3 14 5 22 1 4 5 4 6 0l3-12c1-3 5-3 6 0l3 12c1 4 5 4 6 0 2-8 2-16 5-22 4-8 2-18-4-20-6-2-10 2-13 2s-7-4-13-2z"/></svg><h3>Emergency Services</h3><p>It is a long established fact that a will be distracted.</p><a class="btn">View Details</a></div>
<div class="svc" style="left:228px;top:1875px"><svg width="64" height="70" viewBox="0 0 64 70" fill="none" stroke="#9a877c" stroke-width="2"><path d="M14 8c-6 2-8 12-4 20 3 6 3 14 5 22 1 4 5 4 6 0l3-12c1-3 5-3 6 0l3 12c1 4 5 4 6 0 2-8 2-16 5-22 4-8 2-18-4-20-6-2-10 2-13 2s-7-4-13-2z"/></svg><h3>Dental Hygiene</h3><p>It is a long established fact that a will be distracted.</p><a class="btn">View Details</a></div>
<div class="svc" style="left:494px;top:1875px"><svg width="64" height="70" viewBox="0 0 64 70" fill="none" stroke="#9a877c" stroke-width="2"><path d="M14 8c-6 2-8 12-4 20 3 6 3 14 5 22 1 4 5 4 6 0l3-12c1-3 5-3 6 0l3 12c1 4 5 4 6 0 2-8 2-16 5-22 4-8 2-18-4-20-6-2-10 2-13 2s-7-4-13-2z"/></svg><h3>Dentures</h3><p>It is a long established fact that a will be distracted.</p><a class="btn">View Details</a></div>
<div class="svc" style="left:758px;top:1875px"><svg width="64" height="70" viewBox="0 0 64 70" fill="none" stroke="#9a877c" stroke-width="2"><path d="M14 8c-6 2-8 12-4 20 3 6 3 14 5 22 1 4 5 4 6 0l3-12c1-3 5-3 6 0l3 12c1 4 5 4 6 0 2-8 2-16 5-22 4-8 2-18-4-20-6-2-10 2-13 2s-7-4-13-2z"/></svg><h3>Restorations</h3><p>It is a long established fact that a will be distracted.</p><a class="btn">View Details</a></div>

<!-- Testimonials -->
<p class="abs eyebrow center" style="top:2280px">Our Testimonial</p>
<h2 class="abs section-title center" style="top:2307px">Pleasing Patients Is Our Greatest Achievement</h2>
<p class="abs section-sub center" style="top:2356px">Welcome to our Maplecrest Chapters dedicated to empowering pet owners with<br>valuable knowledge and resources.</p>
<svg class="abs arc" width="1200" height="4231" viewBox="0 0 1200 4231" fill="none"><path d="M262 2735 A338 300 0 0 1 938 2735" stroke="#efece9" stroke-width="30" stroke-linecap="round"/></svg>
<div class="abs doc-photo" role="img" aria-label="Smiling dentist with arms crossed beside a tooth model"></div>

<div class="quote" style="left:276px;top:2449px"><h4>Maren T.</h4><p>It is a long established fact that a reader will be distracted by the of using Lorem Ipsum.</p><i>“</i></div>
<div class="quote" style="left:701px;top:2449px"><h4>Maren T.</h4><p>It is a long established fact that a reader will be distracted by the of using Lorem Ipsum.</p><i>“</i></div>
<div class="quote" style="left:156px;top:2613px"><h4>Maren T.</h4><p>It is a long established fact that a reader will be distracted by the of using Lorem Ipsum.</p><i>“</i></div>
<div class="quote" style="left:824px;top:2613px"><h4>Maren T.</h4><p>It is a long established fact that a reader will be distracted by the of using Lorem Ipsum.</p><i>“</i></div>

<!-- Team -->
<section class="abs team-bg"></section>
<p class="abs eyebrow center" style="top:2960px">Meet Our Dental Team</p>
<h2 class="abs section-title center" style="top:2987px">COMMITTED TO YOUR SMILE</h2>
<p class="abs section-sub center" style="top:3034px">Welcome to our Maplecrest Chapters dedicated to empowering pet owners with<br>valuable knowledge and resources.</p>

<div class="member" style="left:161px"><div class="photo" role="img" aria-label="Dentist portrait" style="background:linear-gradient(180deg,#e8eef3,#7ea6cc)"></div><div class="tag"><b>Dr. Nora Whitley</b><small>Lead Dentist</small></div></div>
<div class="member" style="left:386px"><div class="photo" role="img" aria-label="Dentist portrait" style="background:linear-gradient(180deg,#c9ced2,#eceef0)"></div><div class="tag"><b>Dr. Nora Whitley</b><small>Lead Dentist</small></div></div>
<div class="member" style="left:611px"><div class="photo" role="img" aria-label="Dentist portrait" style="background:linear-gradient(180deg,#4cc3d9,#2a8fb4)"></div><div class="tag"><b>Dr. Nora Whitley</b><small>Lead Dentist</small></div></div>
<div class="member" style="left:837px"><div class="photo" role="img" aria-label="Dentist portrait" style="background:linear-gradient(180deg,#e9ecef,#c3ccd6)"></div><div class="tag"><b>Dr. Nora Whitley</b><small>Lead Dentist</small></div></div>
<a class="btn team-btn">View All Team</a>

<!-- Booking -->
<section class="abs book-band"></section>
<div class="abs map" role="img" aria-label="Street map showing the clinic location"></div>
<h2 class="abs book-title">BOOK AN APPOINTMENT</h2>
<div class="field" style="left:614px;top:3616px;width:200px;height:36px">First Name</div>
<div class="field" style="left:829px;top:3616px;width:202px;height:36px">Last Name</div>
<div class="field" style="left:614px;top:3667px;width:200px;height:35px">Email Address</div>
<div class="field" style="left:829px;top:3667px;width:202px;height:35px">Phone Number</div>
<div class="field" style="left:614px;top:3718px;width:417px;height:130px">Message</div>
<a class="btn book-btn">Book Your Appointment</a>

<!-- Footer -->
<div class="abs logo foot-logo"><div class="name">Harrowfield</div><div class="sub">DENTISTRY</div></div>
<nav class="abs foot-nav"><a href="#">Home</a><a href="#">About Us</a><a href="#">Services</a><a href="#">Team</a><a href="#">Contact Us</a></nav>
<div class="contact" style="left:280px"><span class="ci"><svg width="14" height="14" viewBox="0 0 24 24" fill="#fff"><path d="M6.6 10.8a15.1 15.1 0 0 0 6.6 6.6l2.2-2.2a1 1 0 0 1 1-.25 11.4 11.4 0 0 0 3.6.57 1 1 0 0 1 1 1V20a1 1 0 0 1-1 1A17 17 0 0 1 3 4a1 1 0 0 1 1-1h3.5a1 1 0 0 1 1 1c0 1.25.2 2.45.57 3.57a1 1 0 0 1-.25 1z"/></svg></span>+1 555 014 7788</div>
<div class="contact" style="left:487px"><span class="ci"><svg width="14" height="14" viewBox="0 0 24 24" fill="none" stroke="#fff" stroke-width="2"><rect x="3" y="5" width="18" height="14" rx="2"/><path d="M3 7l9 6 9-6"/></svg></span>hello@harrowfielddental.com</div>
<div class="contact" style="left:746px"><span class="ci"><svg width="14" height="14" viewBox="0 0 24 24" fill="#fff"><path d="M12 2a7 7 0 0 0-7 7c0 5 7 13 7 13s7-8 7-13a7 7 0 0 0-7-7zm0 9.5A2.5 2.5 0 1 1 12 6.5a2.5 2.5 0 0 1 0 5z"/></svg></span>48 Linden Row, Fairhaven</div>
<div class="abs social"><span></span><span></span><span></span></div>

</body>
</html>
```